kolvarin.link kolvarin.space kolvarin.press website

The website is named KOLVARIN and it will have 3 domain names. kolvarin.link, press, space.
I'd like it to be viewed on Pads, pcs and phones.

page menu:

kolvarin.link(start page): presentation of company. (creative, design, app, new product innovation.)
Here we'll need sosial media icons: plimber, vendoloop, mirtavel, trelvanet. (light but some 'fruity' colors)

kolvarin.press: blog. It will be a 75% picture blog > rest will be text. I need to be able to resize pictures and shape columns to picture size. (light but some 'fruity' colors)

kolvarin.space : the fun part of this web design, however, on entering the page I'd like a non-disclosure agreement where viewer simply click "yes, I agree" after filling out contact info. (check attached document)
We will have space here for uploading PDF files viewers can download. There is also a blog space here to tell in brief about the PDF file. (maybe a space/sci-fi theme her e.g spacechimp, Laika the space dog?)

I will attach the logo here I want you to use > and develop for the .space .press webpage. The logo i uploaded is for the .link page.

Target Market(s)

venture capitalists

Number of Pages Required

3 page

Requirements
Must have
• a few 'fruity colors' but mostly white and grey

```html
<!DOCTYPE html>
<html lang="en">
<head>
<meta charset="utf-8">
<title>kolvarin.link</title>
<link rel="stylesheet" href="https://fonts.googleapis.com/css2?family=Open+Sans:wght@400;600;700&family=Silkscreen:wght@400;700&family=Oswald:wght@500&display=swap">
<style>
:root{
  --green:#2b6e37;
  --green-dark:#24602f;
  --green-foot:#2c7a33;
  --red:#e0533b;
  --ink:#333;
  --muted:#666;
  --grey-band:#f2f2f2;
  --white:#fff;
  --plimber:#5cbf3a;
  --mirtavel:#1f77c9;
  --vendoloop:#9a4a1f;
  --trelvanet:#2f7d1d;
  --orange:#f0a21b;
}
*{box-sizing:border-box;margin:0;padding:0}
html,body{width:1200px;height:2206px;overflow:hidden}
body{position:relative;font-family:"Open Sans",sans-serif;color:var(--ink);background:var(--white)}
.abs{position:absolute}
.topline{left:0;top:0;width:1200px;height:4px;background:var(--green)}
.logo{left:98px;top:30px;font-family:"Open Sans",sans-serif;font-weight:700;font-size:22px;color:var(--ink);display:flex;align-items:center;gap:8px;height:80px}
.logo .mark{width:20px;height:20px;background:var(--orange)}
.social{display:flex;gap:6px}
.social .s{width:32px;height:32px;border-radius:6px;overflow:hidden;color:transparent;font-size:1px}
.s.plimber{background:var(--plimber)}.s.mirtavel{background:var(--mirtavel)}.s.vendoloop{background:var(--vendoloop)}.s.trelvanet{background:var(--trelvanet)}
.header-social{left:635px;top:50px}
.search{left:791px;top:47px;width:309px;height:38px;border:1px solid #ccc;display:flex}
.search span{flex:1;font-size:12px;color:#555;padding:10px 12px}
.search i{width:45px;background:var(--orange);display:flex;align-items:center;justify-content:center}
.hero{left:0;top:137px;width:1200px;height:514px;background:linear-gradient(135deg,#6b4a32 0%,#8a6848 35%,#4a3b30 60%,#7d5a3c 100%)}
.nav{left:100px;top:128px;width:1000px;height:50px;background:linear-gradient(90deg,#2d7a36,#3b8f40);border:2px solid #2a6a31;display:flex;z-index:2;box-shadow:0 2px 4px rgba(0,0,0,.3)}
.nav a{color:var(--white);text-decoration:none;font-size:13px;font-weight:600;display:flex;align-items:center;justify-content:center;flex:1}
.nav a.home{flex:0 0 162px;background:var(--red)}
.hero-title{left:0;top:370px;width:1200px;text-align:center;font-family:"Silkscreen",sans-serif;font-weight:700;font-size:38px;color:var(--white);letter-spacing:2px}
.hero-sub{left:400px;top:418px;width:400px;text-align:center;color:var(--white);font-size:12.5px;line-height:23px}
.btn-red{left:538px;top:475px;width:125px;height:41px;background:var(--red);color:var(--white);font-size:12.5px;display:flex;align-items:center;justify-content:center}
.h2{left:0;width:1200px;text-align:center;font-family:"Silkscreen",sans-serif;font-weight:700;font-size:32px;letter-spacing:3px;color:var(--ink)}
.h2 em{font-style:normal;color:var(--red)}
.welcome-text{left:206px;top:737px;width:785px;text-align:center;font-size:11.5px;line-height:23.5px;color:var(--muted)}
.btn{top:820px;width:191px;height:50px;display:flex;align-items:center;justify-content:center;font-size:15px}
.btn.team{left:391px;background:var(--green);color:var(--white)}
.btn.clients{left:615px;border:1px solid var(--red);color:var(--red)}
.band{left:0;top:948px;width:1200px;height:431px;background:var(--grey-band)}
.work{width:320px;text-align:center}
.work .circle{width:126px;height:126px;border-radius:50%;background:var(--green);margin:0 auto;display:flex;align-items:center;justify-content:center;box-shadow:0 12px 8px -8px rgba(0,0,0,.15)}
.work h3{font-size:16px;font-weight:400;color:var(--ink);margin-top:24px}
.work p{font-size:12.2px;line-height:20.5px;color:var(--muted);margin-top:6px;padding:0 22px}
.card{top:1514px;width:99px;height:99px;background:var(--white);border-radius:6px;box-shadow:0 2px 6px rgba(0,0,0,.25);display:flex;align-items:center;justify-content:center}
.card div{width:56px;height:56px;border-radius:8px}
.arrow{color:#aaa;font-size:28px}
.contact{left:0;top:1690px;width:1200px;height:466px;background:linear-gradient(160deg,#4a4a3e 0%,#5b5a48 40%,#3f4740 100%)}
.contact-title{left:0;top:1722px;width:1200px;text-align:center;font-family:"Oswald",sans-serif;font-size:32px;color:var(--white)}
.field{left:203px;width:272px;border:1px solid #ddd;color:var(--white);font-size:11px;padding:10px 14px;background:rgba(0,0,0,.08)}
.submit{left:203px;top:2068px;width:272px;height:37px;background:var(--green);color:var(--white);font-size:12px;font-weight:700;display:flex;align-items:center;justify-content:center}
.info{left:525px;top:1807px;width:357px;height:250px;background:var(--green);padding:10px}
.info .inner{border:1px solid rgba(255,255,255,.35);height:100%;padding:22px 24px;color:var(--white)}
.info .brand{font-weight:700;font-size:22px;display:flex;align-items:center;gap:8px;margin-bottom:38px}
.info .brand .mark{width:18px;height:18px;background:var(--white)}
.info li{list-style:none;display:flex;align-items:center;gap:12px;font-size:15px;height:32px}
.footer{left:0;top:2156px;width:1200px;height:50px;background:var(--green-foot);color:var(--white);font-size:12px}
.footer .copy{left:98px;top:17px}
.footer .connect{left:770px;top:17px}
.footer .social{position:absolute;left:966px;top:9px}
.footer .code{left:1155px;top:17px;font-size:11px}
</style>
</head>
<body>
<div class="abs topline"></div>

<header>
  <div class="abs logo"><span class="mark"></span>KOLVARIN</div>
  <div class="abs social header-social">
    <span class="s plimber">plimber</span><span class="s mirtavel">mirtavel</span><span class="s vendoloop">vendoloop</span><span class="s trelvanet">trelvanet</span>
  </div>
  <div class="abs search"><span>Enter your keywords...</span><i><svg width="20" height="20" viewBox="0 0 20 20"><circle cx="8" cy="8" r="5.5" fill="none" stroke="#fff" stroke-width="2.5"/><line x1="12" y1="12" x2="17" y2="17" stroke="#fff" stroke-width="3"/></svg></i></div>
  <nav class="abs nav">
    <a class="home" href="#">HOME</a><a href="#">ABOUT US</a><a href="#">HOW IT WORKS</a><a href="#">REWARDS</a><a href="#">CONTACT US</a>
  </nav>
</header>

<section>
  <div class="abs hero" role="img" aria-label="Desk scene with laptop, notebooks, pencils and coffee cup"></div>
  <svg class="abs" style="left:34px;top:368px" width="20" height="52"><polyline points="18,2 2,26 18,50" fill="none" stroke="#fff" stroke-width="2"/></svg>
  <svg class="abs" style="left:1136px;top:368px" width="20" height="52"><polyline points="2,2 18,26 2,50" fill="none" stroke="#fff" stroke-width="2"/></svg>
  <div class="abs hero-title">CREATIVE DESIGN</div>
  <div class="abs hero-sub">Lorem Ipsum is simply dummy text of the printing and typesetting industry. Lorem Ipsum has been the industry's</div>
  <div class="abs btn-red">View more</div>
</section>

<section>
  <div class="abs h2" style="top:682px">WELCOME TO <em>KOLVARIN.LINK</em></div>
  <p class="abs welcome-text">Lorem Ipsum is simply dummy text of the printing and typesetting industry. Lorem Ipsum has been the industry's standard dummy text ever since the 1500s, when an unknown printer took a galley of type and scrambled it to make a type specimen book. It has survived not only five centuries, but also the leap into electronic typesetting, remaining essentially unchanged</p>
  <div class="abs btn team">Meet our Team</div>
  <div class="abs btn clients">Visit our Clients</div>
</section>

<section>
  <div class="abs band"></div>
  <div class="abs h2" style="top:1001px">HOW IT <em>WORKS</em></div>
  <div class="abs work" style="left:96px;top:1082px">
    <div class="circle"><svg width="50" height="44" viewBox="0 0 50 44"><rect x="1" y="1" width="48" height="32" rx="3" fill="#fff"/><rect x="6" y="6" width="38" height="22" fill="#2b6e37"/><rect x="20" y="33" width="10" height="6" fill="#fff"/><rect x="14" y="39" width="22" height="4" fill="#fff"/></svg></div>
    <h3>DISPLAY ADVERTISING</h3>
    <p>Display advertising is one of the most effective ways to reach relevant audiences at scale. The amount of available</p>
  </div>
  <div class="abs work" style="left:440px;top:1082px">
    <div class="circle"><svg width="50" height="32" viewBox="0 0 50 32"><rect x="0" y="0" width="32" height="32" rx="5" fill="#fff"/><polygon points="34,10 50,1 50,31 34,22" fill="#fff"/></svg></div>
    <h3>VIDEO AD ADVERTISING</h3>
    <p>Display advertising is one of the most effective ways to reach relevant audiences at scale. The amount of available</p>
  </div>
  <div class="abs work" style="left:771px;top:1082px">
    <div class="circle"><svg width="38" height="46" viewBox="0 0 38 46"><polygon points="2,2 26,2 36,12 36,44 2,44" fill="none" stroke="#fff" stroke-width="3"/><line x1="9" y1="20" x2="29" y2="20" stroke="#fff" stroke-width="3"/><line x1="9" y1="28" x2="29" y2="28" stroke="#fff" stroke-width="3"/><line x1="9" y1="36" x2="29" y2="36" stroke="#fff" stroke-width="3"/></svg></div>
    <h3>DSP ADVERTISING</h3>
    <p>Display advertising is one of the most effective ways to reach relevant audiences at scale. The amount of available</p>
  </div>
</section>

<section>
  <div class="abs h2" style="top:1428px">LATEST <em>APPS</em></div>
  <div class="abs arrow" style="left:101px;top:1540px">&#8249;</div>
  <div class="abs arrow" style="left:1090px;top:1540px">&#8250;</div>
  <div class="abs card" style="left:173px"><div role="img" aria-label="Pineapple app icon" style="background:#f0a21b"></div></div>
  <div class="abs card" style="left:349px"><div role="img" aria-label="Strawberry app icon" style="background:#e03a2a"></div></div>
  <div class="abs card" style="left:532px"><div role="img" aria-label="Plum app icon" style="background:#6a2d3a"></div></div>
  <div class="abs card" style="left:715px"><div role="img" aria-label="Grapes app icon" style="background:#7cc23a"></div></div>
  <div class="abs card" style="left:908px"><div role="img" aria-label="Papaya app icon" style="background:#e0892a"></div></div>
</section>

<section>
  <div class="abs contact" role="img" aria-label="Street map of a city district"></div>
  <div class="abs contact-title">CONTACT US</div>
  <div class="abs field" style="top:1808px;height:37px">Name :</div>
  <div class="abs field" style="top:1860px;height:36px">Email :</div>
  <div class="abs field" style="top:1911px;height:37px">Phone :</div>
  <div class="abs field" style="top:1965px;height:89px">Message :</div>
  <div class="abs submit">SUBMIT</div>
  <div class="abs info">
    <div class="inner">
      <div class="brand"><span class="mark"></span>KOLVARIN</div>
      <ul>
        <li><svg width="12" height="16" viewBox="0 0 12 16"><path d="M6 0a6 6 0 0 0-6 6c0 4 6 10 6 10s6-6 6-10a6 6 0 0 0-6-6zm0 8.5A2.5 2.5 0 1 1 6 3.5a2.5 2.5 0 0 1 0 5z" fill="#fff"/></svg>418 Marrow Lane, Ashgrove, NC 27519</li>
        <li><svg width="16" height="12" viewBox="0 0 16 12"><rect width="16" height="12" rx="1" fill="#fff"/><polyline points="1,1 8,7 15,1" fill="none" stroke="#2b6e37" stroke-width="1.5"/></svg>info@tressaloop.com</li>
        <li><svg width="14" height="14" viewBox="0 0 14 14"><path d="M3 0l2.5 3.5-1.5 2c1 2 2.5 3.5 4.5 4.5l2-1.5L14 11l-1.5 3C6 14 0 8 0 1.5z" fill="#fff"/></svg>5550142873</li>
      </ul>
    </div>
  </div>
</section>

<footer class="abs footer">
  <div class="abs copy">kolvarin.link &copy; 2016. All Rights Reserved</div>
  <div class="abs connect">Connect with our social network :</div>
  <div class="social">
    <span class="s plimber">plimber</span><span class="s mirtavel">mirtavel</span><span class="s vendoloop">vendoloop</span><span class="s trelvanet">trelvanet</span>
  </div>
  <div class="abs code">C12</div>
</footer>
</body>
</html>
```